Business Card for Coastal Tundrabridge Advisory

We need a business card for Coastal Tundrabridge Advisory. The company website address is provided below. The company logo is attached. We provide specialized permafrost services to the mining, transportation, and oil & gas industries. The card should be prepared for:
Matthias Korhonen, PhD.
Coastal Tundrabridge Advisory
PO Box 418259
Quillwater, Alaska 99642
Direct: +1-907-555-0143
Email: mkorhonen@tundrabridgeadvisory.example
Website: www.coastaltundrabridgeadvisory.example

```html
<!DOCTYPE html>
<html lang="en">
<head>
<meta charset="utf-8">
<title>Coastal Tundrabridge Advisory – Business Card</title>
<link rel="stylesheet" href="https://fonts.googleapis.com/css2?family=Montserrat:wght@400;500;600;700&display=swap">
<style>
  :root {
    --stage: #e9e7e3;
    --card-white: #ffffff;
    --ink: #1f262c;
    --band-dark: #2f2f31;
    --band-grey: #6a6a6c;
    --text-light: #ffffff;
    --back-top: #2a2a2c;
    --back-bottom: #0e0e0f;
  }
  * { box-sizing: border-box; margin: 0; padding: 0; }
  html, body {
    width: 900px; height: 1200px; overflow: hidden;
    background: var(--stage);
    font-family: "Montserrat", sans-serif;
  }
  .canvas { position: relative; width: 900px; height: 1200px; }

  .card {
    position: absolute; left: 80px; width: 742px; height: 441px;
    border-radius: 36px; overflow: hidden;
    box-shadow: 0 6px 14px rgba(0,0,0,.25);
  }
  .card-front { top: 131px; background: var(--card-white); }
  .card-back {
    top: 638px;
    background: linear-gradient(135deg, var(--back-top) 0%, var(--back-bottom) 70%);
  }

  .brand-name {
    position: absolute; left: 56px; top: 64px;
    font-weight: 600; font-size: 30px; letter-spacing: 2px;
    color: var(--ink); text-transform: uppercase;
  }

  .person { position: absolute; left: 38px; top: 236px; color: var(--ink); }
  .person-name { font-weight: 700; font-size: 27px; line-height: 1.1; }
  .person-title { font-weight: 400; font-size: 16px; margin-top: 4px; }

  .contact-band { position: absolute; left: 0; top: 302px; width: 742px; height: 103px; }

  .contact-list {
    position: absolute; left: 44px; top: 320px; list-style: none;
    color: var(--text-light); font-size: 15.5px; line-height: 22.5px;
  }
  .contact-list li { display: flex; align-items: center; gap: 10px; }
  .contact-list svg { width: 16px; height: 14px; fill: var(--text-light); flex: none; }

  .address {
    position: absolute; left: 518px; top: 352px;
    color: var(--text-light); font-size: 16px; line-height: 21px;
  }

  .back-brand {
    position: absolute; left: 0; right: 0; top: 0; bottom: 0;
  }
  .back-name {
    position: absolute; left: 365px; top: 358px;
    color: var(--text-light); font-weight: 600; font-size: 14px; letter-spacing: 1.5px;
    text-transform: uppercase;
  }
</style>
</head>
<body>
<main class="canvas">

  <section class="card card-front" aria-label="Business card front">
    <div class="brand-name">Coastal Tundrabridge Advisory</div>

    <div class="person">
      <div class="person-name">Matthias Korhonen, PhD.</div>
      <div class="person-title">CEO &amp; Founder</div>
    </div>

    <svg class="contact-band" viewBox="0 0 742 103" aria-hidden="true">
      <polygon points="0,0 519,0 460,103 0,103" fill="var(--band-dark)"/>
      <polygon points="531,0 742,0 742,103 472,103" fill="var(--band-grey)"/>
    </svg>

    <ul class="contact-list">
      <li>
        <svg viewBox="0 0 16 14"><path d="M1 5c0-2 2-4 7-4s7 2 7 4l-3 1-1-2H5L4 6 1 5zm3 2h8l2 6H2l2-6zm4 1.5a2 2 0 100 4 2 2 0 000-4z"/></svg>
        <span>+1-907-555-0143</span>
      </li>
      <li>
        <svg viewBox="0 0 16 14"><path d="M1 2h14v1L8 8 1 3V2zm0 3l7 5 7-5v7H1V5z"/></svg>
        <span>mkorhonen@tundrabridgeadvisory.example</span>
      </li>
      <li>
        <svg viewBox="0 0 16 14"><circle cx="8" cy="7" r="6.5"/><path d="M5 3l3 2-1 3 2 2-1 3M11 2l-1 3 3 1" stroke="var(--band-dark)" stroke-width="1.2" fill="none"/></svg>
        <span>www.coastaltundrabridgeadvisory.example</span>
      </li>
    </ul>

    <address class="address" style="font-style:normal">
      PO Box 418259<br>
      Quillwater, Alaska 99642
    </address>
  </section>

  <section class="card card-back" aria-label="Business card back">
    <div class="back-brand" role="img" aria-label="Dark glossy background with faint repeated company name pattern"></div>
    <div class="back-name">Coastal Tundrabridge Advisory</div>
  </section>

</main>
</body>
</html>
```